Single-sided business card for restaurant velmora with new logo made on this site

Business card options with new logo including restaurant name, address, phone number and website. This business card is single-sided only and will be presented at the hostess desk for clients to take. I would like to see options based on a cream card background, a white card background, a yellow card background and a burgundy colored background. It needs to be elegant and traditional.

Target Market(s)

local and international crowd

Industry/Entity Type

restaurant

Contact Information for Business Card

address, website and phone number

Font styles to use
Serif

Colors
EE7325
F08F49
F5BC92
FAE3D3
FDF4ED

Requirements
Must have
• new logo, address, phone number, website
Should not have
• more than three colors

```html
<!DOCTYPE html>
<html lang="es">
<head>
<meta charset="utf-8">
<title>Velmora – Tarjeta de presentación</title>
<link rel="stylesheet" href="https://fonts.googleapis.com/css2?family=Montserrat:wght@400;500&display=swap">
<style>
  :root {
    --stage: #2a2a2a;
    --card-yellow: #f8b52d;
    --ink-brown: #3b1a17;
  }
  * { margin: 0; padding: 0; box-sizing: border-box; }
  html, body {
    width: 1200px; height: 800px; overflow: hidden;
    background: var(--stage);
  }
  .card {
    position: absolute; left: 80px; top: 105px;
    width: 1040px; height: 590px;
    background: var(--card-yellow);
    font-family: "Montserrat", sans-serif;
    color: var(--ink-brown);
    overflow: hidden;
  }
  .card__frame {
    position: absolute; inset: 28px 28px 28px 30px;
    border: 4px solid var(--ink-brown);
  }
  .card__decor {
    position: absolute; left: 320px; top: 90px;
    width: 700px; height: 480px;
    background: radial-gradient(ellipse at 60% 85%, rgba(244,150,30,0.55) 0%, rgba(244,162,38,0.25) 45%, rgba(248,181,45,0) 75%);
  }
  .brand {
    position: absolute; left: 210px; top: 192px; width: 230px;
    text-align: center;
  }
  .brand__mark {
    display: block; width: 128px; height: 128px; margin: 0 auto;
    background: var(--ink-brown);
  }
  .brand__name {
    margin-top: 22px;
    font-size: 36px; font-weight: 500; letter-spacing: 6px;
    line-height: 1;
  }
  .card__divider {
    position: absolute; left: 468px; top: 160px;
    width: 2px; height: 268px; background: var(--ink-brown);
  }
  .contact {
    position: absolute; left: 508px; top: 184px;
    font-size: 22px; font-weight: 400; line-height: 29px;
    font-style: normal;
  }
  .contact__label { margin-top: 10px; }
  .contact__phone { font-size: 30px; line-height: 38px; font-weight: 500; }
  .contact__web { margin-top: 12px; font-size: 21px; letter-spacing: 0.5px; }
</style>
</head>
<body>
  <section class="card">
    <div class="card__decor" role="img" aria-label="Soft orange foliage decoration fading into the card"></div>
    <div class="card__frame"></div>

    <div class="brand">
      <span class="brand__mark"></span>
      <p class="brand__name">VELMORA</p>
    </div>

    <div class="card__divider"></div>

    <address class="contact">
      <p>Restaurant Velmora</p>
      <p>Jacaranda 415</p>
      <p>Bahías de Huatulco</p>
      <p>Oaxaca CP 70989</p>
      <p class="contact__label">Reservaciones</p>
      <p class="contact__phone">958-412-3078</p>
      <p class="contact__web">www.velmora.com.mx</p>
    </address>
  </section>
</body>
</html>
```